Design einer Kundenkarte für Handelsunternehmen
Zielgruppe
Wir sind ein Handelsunternehmen für Afro Kosmetik und für Kosmetik für Menschen mit lockigem Haar. Wir wollen eine Kundenkarte mit verschiedenen Levels herausbringen.
Aufgabenstellung
Die Kundenkarte hat verschiedene Levels für jedes Level soll ein eigenes Kartendesign entwickelt werden.
Level 1 = Lady/Sir = Ist eine kostenlose Karte, die jeder bekommen kann
Level 2 = Contessa/Conte = ist eine Karte, die an einen bestimmten Umsatz gebunden ist
Level 3 = Princes/Prince = ist eine Karte, die an einen Höheren Umsatz gebunden ist.
Level 4 = Queen/King = ist eine Karte, die an einen noch höheren Umsatz gebunden ist
Level 5 = Profesional = Ist eine Karte, die nur an gewerbliche Kunden herausgegeben wird.
Die Kundenkarte wird auf eine NFC Karte gedruckt,
Folgende Elemente soll die Kundenkarte beinhalten:
Vorderseite der Karte:
Vorname und Nachname des Kunden
Kundennummer
Kartennummer
Kundennummer als QR Code
Gültigkeit bis MM/JJJJ
Foto des Kunden
Rückseite der Karte
Unterschriftsfeld
Sicherheitscode soll auf der Rückseite

```html
<!DOCTYPE html>
<html lang="de">
<head>
<meta charset="utf-8">
<title>Kundenkarte L2 – Entwurf</title>
<link rel="stylesheet" href="https://fonts.googleapis.com/css2?family=Quicksand:wght@500;600&family=Source+Sans+3:wght@400;500&family=Caveat+Brush&display=swap">
<style>
  :root {
    --sheet: #ffffff;
    --ink: #111111;
    --slate-light: #9a9ea1;
    --slate-dark: #4f5457;
    --sand: #e4ddd0;
    --apricot: #e89f74;
    --gold-soft: #cbb38a;
    --cocoa: #6d5a45;
    --black: #000000;
    --amber: #f0a020;
    --white: #ffffff;
    --photo-skin: #8a5a3c;
    --photo-hair: #2e1f17;
  }
  * { box-sizing: border-box; margin: 0; padding: 0; }
  html, body { width: 849px; height: 1200px; overflow: hidden; background: var(--sheet); }
  body { position: relative; font-family: "Source Sans 3", sans-serif; color: var(--ink); }

  .sheet-title { position: absolute; left: 45px; top: 29px; font-size: 16px; line-height: 21px; font-weight: 400; }
  .variant-label { position: absolute; font-size: 15px; }
  .variant-label.a { left: 182px; top: 261px; }
  .variant-label.b { left: 176px; top: 778px; }

  .card { position: absolute; left: 377px; width: 337px; height: 218px; border-radius: 17px; overflow: hidden; }

  .brand { position: absolute; font-family: "Quicksand", sans-serif; font-weight: 500; font-size: 27px; letter-spacing: 0.5px; white-space: nowrap; }
  .tagline { position: absolute; right: 17px; text-align: right; font-family: "Caveat Brush", cursive; line-height: 1; }

  /* Variante A – Vorderseite */
  .front-a { top: 73px; background: linear-gradient(100deg, var(--photo-hair) 0%, var(--photo-skin) 18%, #3a3a3c 34%, var(--slate-dark) 45%, var(--slate-light) 75%, #8e9396 100%); }
  .front-a .brand { right: 17px; top: 36px; color: var(--white); }
  .front-a .tagline { top: 147px; color: var(--gold-soft); font-size: 22px; }

  /* Variante A – Rückseite */
  .back-a { top: 329px; background: var(--sand); }
  .back-a .stripe { position: absolute; left: 0; right: 0; bottom: 0; height: 32px; background: var(--apricot); border-radius: 14px 14px 0 0; }

  /* Variante B – Vorderseite */
  .front-b { top: 649px; background: var(--white); border: 1px solid #e3e3e3; }
  .front-b .model-photo { position: absolute; left: 0; top: 0; width: 150px; height: 100%; background: linear-gradient(90deg, var(--photo-hair) 0%, var(--photo-skin) 45%, #c9a589 75%, rgba(255,255,255,0) 100%); }
  .front-b .brand { right: 17px; top: 26px; color: var(--ink); }
  .front-b .tagline { top: 140px; color: var(--cocoa); font-size: 28px; }

  /* Variante B – Rückseite */
  .back-b { top: 904px; background: var(--black); color: var(--white); }
  .back-b .signature-field { position: absolute; left: 17px; top: 172px; width: 302px; height: 34px; background: var(--white); border: 2px solid var(--amber); border-radius: 12px; }

  /* Gemeinsame Elemente der Rückseiten */
  .back .brand { left: 17px; top: 26px; }
  .back-a .brand { color: var(--ink); }
  .back-b .brand { color: var(--white); }
  .holder-name { position: absolute; left: 16px; font-family: "Quicksand", sans-serif; font-weight: 600; font-size: 16px; line-height: 22px; }
  .back-a .holder-name { top: 86px; }
  .back-b .holder-name { top: 79px; }
  .customer-data { position: absolute; left: 16px; font-size: 10.5px; line-height: 17px; }
  .back-a .customer-data { top: 139px; }
  .back-b .customer-data { top: 131px; }
  .validity { position: absolute; right: 17px; text-align: right; font-size: 10px; line-height: 13px; }
  .back-a .validity { top: 151px; }
  .back-b .validity { top: 150px; }
  .holder-photo { position: absolute; left: 220px; top: 18px; width: 98px; height: 119px; background: linear-gradient(180deg, var(--photo-hair) 0%, var(--photo-skin) 40%, #a46a48 70%, var(--photo-hair) 100%); }
</style>
</head>
<body>
  <header class="sheet-title">DL_Kundenkarte_Version neu<br>L2</header>

  <span class="variant-label a">A</span>
  <span class="variant-label b">B</span>

  <section class="card front-a" role="img" aria-label="Foto: lächelnde Frau im Blazer vor grauer Wand, zeigt auf den Markennamen">
    <span class="brand">Amali-Noor</span>
    <p class="tagline">Premium<br>Member Card</p>
  </section>

  <section class="card back back-a">
    <span class="brand">Amali-Noor</span>
    <div class="holder-photo" role="img" aria-label="Passfoto des Karteninhabers"></div>
    <p class="holder-name">Loredane<br>Musterlady</p>
    <p class="customer-data">Kundennr.: xxxxxxxxxxxxxx<br>CODE: XAIAG MAEIG</p>
    <p class="validity">Gültig bis: xx 20xx<br>Sicherheitscode: xxxxxxxxxx</p>
    <div class="stripe"></div>
  </section>

  <section class="card front-b">
    <div class="model-photo" role="img" aria-label="Foto: lachende Frau mit lockigem Haar auf weißem Grund"></div>
    <span class="brand">Amali-Noor</span>
    <p class="tagline">Premium<br>Member Card</p>
  </section>

  <section class="card back back-b">
    <span class="brand">Amali-Noor</span>
    <div class="holder-photo" role="img" aria-label="Passfoto des Karteninhabers"></div>
    <p class="holder-name">Loredane<br>Musterlady</p>
    <p class="customer-data">Kundennr.: xxxxxxxxxxxxxx<br>CODE: XAIAG MAEIG</p>
    <p class="validity">Gültig bis: xx 20xx</p>
    <div class="signature-field" aria-label="Unterschriftsfeld"></div>
  </section>
</body>
</html>
```